Commercial Real Estate Appraisal Company needs a postcard design

We need a postcard design for a commercial real estate company based out of Ballston Lake, New York called "Harborline Appraisers".

Harborline Appraisers, LLC., provides high quality commercial appraisal and real estate consulting services to our clients. Our company provides appraisal services for financial lending institutions, real estate developers, local municipalities, attorney’s, private individuals and businesses. Significant capital expenditures were made to ensure we can provide top of the line data research and research publications, as well as, generate our reports with industry leading appraisal software for increased accuracy and efficiency.

Services we provide

Advisory & Consulting Services, Net Lease Valuation, Capitalization Rate Consultation, Operating Expense Consultation, Discounted Cash Flow Analysis, Portfolio Valuation, Expert Witness Services, Property and Comparable Analyses, Financial Feasibility Studies, Property Tax Services, Going Concern Valuations, Real Estate Due Diligence Analyses, Highest and Best Use Studies, Real Estate Valuation, Lease Versus Purchase Analyses, Rent Arbitration and Consultation, Market Rent Analyses, Sale Lease-Backs Analysis, Market Studies, Site Inspections, Divorce Proceedings, Probate / Estate Matters

Please save room on the card for postage and addressing

Industry/Entity Type

Real Estate

```html
<!DOCTYPE html>
<html lang="en">
<head>
<meta charset="utf-8">
<title>Harborline Appraisers Postcard</title>
<link rel="stylesheet" href="https://fonts.googleapis.com/css2?family=Lato:wght@300;400;700&display=swap">
<style>
  :root {
    --stage: #2b2b2b;
    --paper: #ffffff;
    --ink: #1f2a44;
    --text: #555b66;
    --headline: #3a3f4a;
    --accent: #1a73c6;
    --photo-top: #8fb6dc;
    --photo-mid: #5b7fa6;
    --photo-low: #3c4c63;
    --postage: #d9d9d9;
  }
  * { box-sizing: border-box; margin: 0; padding: 0; }
  html, body { width: 1200px; height: 750px; overflow: hidden; }
  body {
    background: var(--stage);
    font-family: "Lato", sans-serif;
    position: relative;
  }

  /* Back of card */
  .card-back {
    position: absolute; left: 144px; top: 52px;
    width: 604px; height: 392px;
    background: var(--paper);
  }
  .card-back .top-band {
    position: absolute; left: 0; top: 0; width: 100%; height: 173px;
    background: var(--paper);
    box-shadow: 0 6px 10px rgba(0,0,0,0.08);
  }
  .brand-back {
    position: absolute; left: 30px; top: 50px; width: 220px;
    display: flex; flex-direction: column; align-items: center; gap: 18px;
  }
  .brand-mark {
    width: 46px; height: 46px; border-radius: 50%;
    background: var(--ink);
  }
  .brand-name {
    font-family: "Lato", sans-serif;
    font-weight: 400; color: var(--ink);
    font-size: 19px; letter-spacing: 1px; white-space: nowrap;
  }
  .services {
    position: absolute; left: 270px; top: 34px; width: 214px;
  }
  .services h2 {
    font-weight: 700; font-size: 17px; color: var(--ink); margin-bottom: 6px;
  }
  .services p {
    font-size: 7.2px; line-height: 1.3; color: var(--text); text-align: justify;
  }
  .postage-box {
    position: absolute; left: 506px; top: 10px; width: 88px; height: 86px;
    background: linear-gradient(180deg, #ececec, var(--postage));
  }
  .contact {
    position: absolute; left: 22px; top: 226px; width: 226px;
    display: flex; flex-direction: column; align-items: center; gap: 8px;
  }
  .phone {
    display: flex; align-items: center; gap: 4px;
    font-size: 24px; color: var(--headline);
  }
  .phone svg { width: 30px; height: 30px; }
  .website {
    background: var(--accent); color: #fff;
    font-size: 14px; padding: 3px 5px;
  }

  /* Front of card */
  .card-front {
    position: absolute; left: 424px; top: 257px;
    width: 644px; height: 417px;
    background: var(--paper);
    box-shadow: -6px 6px 18px rgba(0,0,0,0.35);
    overflow: hidden;
  }
  .hero-photo {
    position: absolute; left: 0; top: 0; width: 100%; height: 304px;
    background: linear-gradient(180deg, var(--photo-top) 0%, var(--photo-mid) 55%, var(--photo-low) 100%);
  }
  .brand-arch {
    position: absolute; left: 0; top: 0; width: 644px; height: 417px;
  }
  .brand-front {
    position: absolute; left: 390px; top: 258px; width: 220px;
    display: flex; flex-direction: column; align-items: center; gap: 32px;
  }
  .brand-front .brand-mark { width: 56px; height: 56px; }
  .brand-front .brand-name { font-size: 19px; }
  .pitch {
    position: absolute; left: 28px; top: 314px; width: 312px;
  }
  .pitch h1 {
    font-weight: 300; font-size: 23px; color: var(--headline);
    letter-spacing: 0.2px; white-space: nowrap; margin-bottom: 5px;
  }
  .pitch p {
    font-size: 7.1px; line-height: 1.25; color: var(--text); text-align: justify;
  }
  .pitch p strong { font-weight: 700; color: var(--ink); }
</style>
</head>
<body>

  <section class="card-back">
    <div class="top-band"></div>
    <div class="brand-back">
      <span class="brand-mark"></span>
      <span class="brand-name">Harborline Appraisers</span>
    </div>
    <div class="services">
      <h2>Services we provide</h2>
      <p>Advisory &amp; Consulting Services, Net Lease Valuation, Capitalization Rate Consultation, Operating Expense Consultation, Discounted Cash Flow Analysis, Portfolio Valuation, Expert Witness Services, Property and Comparable Analyses, Financial Feasibility Studies, Property Tax Services, Going Concern Valuations, Real Estate Due Diligence Analyses, Highest and Best Use Studies, Real Estate Valuation, Lease Versus Purchase Analyses, Rent Arbitration and Consultation, Market Rent Analyses, Sale Lease-Backs Analysis, Market Studies, Site Inspections, Divorce Proceedings, Probate / Estate</p>
    </div>
    <div class="postage-box"></div>
    <div class="contact">
      <div class="phone">
        <svg viewBox="0 0 30 30" aria-hidden="true">
          <circle cx="15" cy="15" r="15" fill="#1a73c6"/>
          <path d="M10.5 7.5c.8-.5 1.7-.2 2.1.6l1.2 2.6c.3.7.1 1.4-.5 1.9l-1 .8c.8 1.9 2.2 3.4 4.1 4.3l.8-1c.5-.6 1.3-.8 2-.4l2.5 1.3c.8.4 1 1.4.5 2.1l-1 1.5c-.6.9-1.7 1.3-2.7 1-5-1.6-8.8-5.5-10.3-10.5-.3-1 .1-2.1 1-2.7z" fill="#fff"/>
        </svg>
        <span>518.555.0142</span>
      </div>
      <div class="website">www.HarborlineAppraisers.com</div>
    </div>
  </section>

  <section class="card-front">
    <div class="hero-photo" role="img" aria-label="Photo of two business people in suits shaking hands in front of a blue glass office tower"></div>
    <svg class="brand-arch" viewBox="0 0 644 417" aria-hidden="true">
      <path d="M430 304 C430 262 462 240 500 240 C538 240 570 262 570 304 L644 304 L644 417 L0 417 L0 304 Z" fill="#ffffff"/>
    </svg>
    <div class="brand-front">
      <span class="brand-mark"></span>
      <span class="brand-name">Harborline Appraisers</span>
    </div>
    <div class="pitch">
      <h1>IS TIME TO GOOD BUSINESS</h1>
      <p><strong>Harborline Appraisers, LLC.</strong> provides high quality commercial appraisal and real estate consulting services to our clients. Our company provides appraisal services for financial lending institutions, real estate developers, local municipalities, attorney’s, private individuals and businesses. Significant capital expenditures were made to ensure we can provide top of the line data research and research publications, as well as, generate our reports with industry leading appraisal software for increased accuracy and efficiency.</p>
    </div>
  </section>

</body>
</html>
```